Small Catering Menu

I am looking to make a small menu for catering for my company. I am thinking of a small A5 size booklet which will also have some pictures and the cover needs to be attractive.
Likely to be 8-12 pages depending upon your design (could be less or more). I need 2-3 pages as proposal concept (Cover, inside first page and one menu page) and if we like it we will make the project guaranteed before finishing the rest of the project to add security for the designer.
Pictures will be provided to the designer whose concept is the best as they are too heavy. But use generic photos for now (rather large ones) if possible.
Logo is available and so is the inside text as well as some other tidbits.
I will provide the fonts too to ensure it maintains the corporate integrity that we are following.
Industry/Entity Type
Catering

```html
<!DOCTYPE html>
<html lang="en">
<head>
<meta charset="utf-8">
<title>Harbor Table Catering – Menu Cover</title>
<link rel="stylesheet" href="https://fonts.googleapis.com/css2?family=Montserrat:wght@400;500;600&display=swap">
<style>
  :root {
    --backdrop: #e9e8e6;
    --band-black: #1b1b1b;
    --brown-core: #6a412b;
    --brown-edge: #4a2d1f;
    --accent-red: #b8361f;
    --paper-white: #f4f2ef;
    --ink-white: #f6f1ea;
    --gold: #d9a038;
  }
  * { box-sizing: border-box; margin: 0; padding: 0; }
  html, body {
    width: 1200px; height: 1000px; overflow: hidden;
    background: var(--backdrop);
    font-family: "Montserrat", Arial, sans-serif;
  }
  .cover {
    position: absolute; left: 290px; top: 62px;
    width: 620px; height: 876px;
    background: var(--band-black);
    box-shadow: 0 6px 18px rgba(0,0,0,0.18);
    overflow: hidden;
  }
  .cover__field {
    position: absolute; left: 0; top: 110px; width: 100%; height: 530px;
    background: radial-gradient(ellipse at 55% 45%, var(--brown-core) 0%, var(--brown-edge) 100%);
  }
  .cover__stripe {
    position: absolute; left: 0; top: 640px; width: 100%; height: 22px; display: flex;
  }
  .cover__stripe-red { width: 47%; background: var(--accent-red); }
  .cover__stripe-white { flex: 1; background: var(--paper-white); }
  .brand-frame {
    position: absolute; left: 85px; top: 65px; width: 450px; height: 280px;
    border: 1.5px solid rgba(246,241,234,0.85);
    display: flex; align-items: center; justify-content: center; gap: 14px;
  }
  .brand-frame__mark {
    width: 22px; height: 22px; background: var(--gold);
  }
  .brand-frame__name {
    color: var(--ink-white); font-weight: 500; font-size: 30px;
    letter-spacing: 1px; text-transform: uppercase;
  }
  .contact {
    position: absolute; left: 0; width: 100%; text-align: center; color: var(--ink-white);
  }
  .contact__phone { top: 380px; font-size: 20px; font-weight: 500; letter-spacing: 0.5px; }
  .contact__email { top: 410px; font-size: 9px; line-height: 12px; opacity: 0.9; }
  .contact__rule {
    position: absolute; left: 150px; top: 450px; width: 320px; height: 1px;
    background: rgba(246,241,234,0.6);
  }
  .contact__web { top: 470px; font-size: 10px; letter-spacing: 4px; opacity: 0.9; }
</style>
</head>
<body>
  <main class="cover">
    <section class="cover__field">
      <div class="brand-frame">
        <span class="brand-frame__mark"></span>
        <span class="brand-frame__name">Harbor Table Catering</span>
      </div>
      <p class="contact contact__phone">800-555-0147</p>
      <p class="contact contact__email">hello@harbortable.com<br>www.harbortable.com</p>
      <div class="contact__rule"></div>
      <p class="contact contact__web">www.harbortablecatering.com</p>
    </section>
    <div class="cover__stripe">
      <span class="cover__stripe-red"></span>
      <span class="cover__stripe-white"></span>
    </div>
  </main>
</body>
</html>
```